Larkspur Talent IT Recruiting firm needs a business card design for Recruiters, Sourcers, and Account

We need business cards that allow us to change all contact info, names, titles (Recruiter, Sourcer, Account Manager, Director, CEO, etc) per person since we have three offices, in three cities, Phoenix, Austin, and Las Vegas. We do recruiting and contractors for IT positions (Developers, Architects, Software Engineers, Security Engineers, Help Desk, DBAs, PMs, Scrum Masters, etc.) Our client companies are very diverse from Meridian 100 to silicone Valley type start-ups.

So, while we what hip, techie, and quirky, it still needs to be professional. Primary color we use is blue, with silver as a secondary color.

Target Market(s)

IT, Technology

Industry/Entity Type

Business

Contact Information for Business Card

Company name: Larkspur Talent, Inc.
Website: www.larkspurtalent.example
Logos for Careerloop, Blipster, and Myriada

Name, Title, Office Number, Cell Number, email

Font styles to use
Serif
Sans Serif

Colors
0455a3
d5d5d5

Requirements
Nice to have
• The grey I selected below is not necessary - but, would like silver included. I included a card design (File 3: LTI early trial example.jpg) that I had started on. It's very rough, and not quite what we're looking for, but what we did like is the logo, big, maybe a bit faded, off center, goes out of frame, etc. Still looking for other ideas - you are the pros! But, just an idea of a design element we liked.

```html
<!DOCTYPE html>
<html lang="en">
<head>
<meta charset="utf-8">
<title>Larkspur Talent — Business Card</title>
<link href="https://fonts.googleapis.com/css2?family=Marcellus&family=Marcellus+SC&family=Open+Sans:wght@400;600&display=swap" rel="stylesheet">
<style>
  :root {
    --backdrop: #1c1c1c;
    --card-white: #ffffff;
    --card-grey: #565656;
    --ink: #2a2a2a;
    --ink-soft: #4a4a4a;
    --brand-blue: #0455a3;
    --brand-sky: #0a92d8;
    --silver: #d5d5d5;
    --silver-faint: #f3f3f3;
  }
  html, body {
    margin: 0;
    padding: 0;
    width: 1200px;
    height: 907px;
    overflow: hidden;
    background: var(--backdrop);
  }
  .canvas {
    position: relative;
    width: 1200px;
    height: 907px;
  }
  .card {
    position: absolute;
    left: 300px;
    width: 600px;
    height: 343px;
    overflow: hidden;
    box-shadow: 0 4px 14px rgba(0,0,0,0.5);
  }
  .card-front { top: 98px; background: var(--card-white); }
  .card-back { top: 475px; background: var(--card-grey); }

  .front-art { position: absolute; inset: 0; }

  .brand {
    position: absolute;
    left: 42px;
    top: 52px;
    width: 300px;
  }
  .brand-name {
    font-family: "Marcellus", serif;
    font-size: 30px;
    letter-spacing: 1px;
    color: var(--brand-blue);
    line-height: 1;
    display: flex;
    align-items: center;
    gap: 8px;
    white-space: nowrap;
  }
  .brand-dot {
    width: 12px;
    height: 12px;
    border-radius: 50%;
    background: var(--brand-sky);
    flex: none;
  }
  .brand-tagline {
    margin-top: 34px;
    font-family: "Marcellus SC", serif;
    font-size: 16px;
    letter-spacing: 2.4px;
    color: var(--ink);
    white-space: nowrap;
  }

  .contacts {
    position: absolute;
    left: 33px;
    top: 250px;
    display: grid;
    grid-template-columns: 148px auto;
    row-gap: 7px;
    font-family: "Open Sans", sans-serif;
    font-size: 13.5px;
    color: var(--ink-soft);
    white-space: nowrap;
  }
  .contact-item { display: flex; align-items: center; gap: 7px; }
  .contact-item svg { width: 14px; height: 14px; fill: var(--brand-blue); flex: none; }

  .person {
    position: absolute;
    right: 30px;
    top: 264px;
    text-align: right;
    color: var(--card-white);
    font-family: "Marcellus", serif;
    white-space: nowrap;
  }
  .person-name { font-size: 21px; line-height: 1.1; }
  .person-title { font-size: 15px; margin-top: 6px; }

  .back-emblem {
    position: absolute;
    left: 200px;
    top: 84px;
    width: 196px;
    height: 196px;
    border-radius: 50%;
    background: var(--card-white);
  }
  .social {
    position: absolute;
    left: 0;
    right: 0;
    top: 136px;
    display: flex;
    justify-content: center;
    gap: 8px;
    font-family: "Open Sans", sans-serif;
    font-size: 11px;
    font-weight: 600;
    color: var(--brand-blue);
  }
</style>
</head>
<body>
<main class="canvas">

  <section class="card card-front" aria-label="Card front">
    <svg class="front-art" viewBox="0 0 600 343" width="600" height="343" aria-hidden="true">
      <defs>
        <linearGradient id="band-gradient" x1="0" y1="0" x2="1" y2="0">
          <stop offset="0" stop-color="#0455a3"/>
          <stop offset="0.5" stop-color="#0a92d8"/>
          <stop offset="1" stop-color="#0455a3"/>
        </linearGradient>
        <linearGradient id="tab-gradient" x1="0" y1="0" x2="1" y2="0">
          <stop offset="0" stop-color="#0a7ccb"/>
          <stop offset="1" stop-color="#0455a3"/>
        </linearGradient>
      </defs>
      <circle cx="490" cy="100" r="110" fill="var(--silver-faint)"/>
      <rect x="0" y="311" width="600" height="32" fill="url(#band-gradient)"/>
      <polygon points="429,256 600,256 600,311 402,311" fill="url(#tab-gradient)"/>
    </svg>

    <div class="brand">
      <div class="brand-name"><span>LARKSPUR TALENT</span><span class="brand-dot"></span></div>
      <div class="brand-tagline">RISING TO THE CHALLENGE</div>
    </div>

    <div class="contacts">
      <div class="contact-item">
        <svg viewBox="0 0 16 16"><path d="M4 1l3 3-2 2c1 2 3 4 5 5l2-2 3 3-2 3C7 15 1 9 1 3z"/></svg>
        <span>555-210-4418</span>
      </div>
      <div class="contact-item">
        <svg viewBox="0 0 16 16"><path d="M2 3h12v10H2z M2 3l6 5 6-5" fill="none" stroke="#0455a3" stroke-width="1.6"/></svg>
        <span>hello@larkspur.example</span>
      </div>
      <div class="contact-item">
        <svg viewBox="0 0 16 16"><rect x="4" y="1" width="8" height="14" rx="1.5"/><rect x="5.5" y="3" width="5" height="6" fill="#fff"/></svg>
        <span>555-367-9024</span>
      </div>
      <div class="contact-item">
        <svg viewBox="0 0 16 16"><circle cx="8" cy="8" r="6.5" fill="none" stroke="#0455a3" stroke-width="1.4"/><path d="M1.5 8h13M8 1.5c-3 3-3 10 0 13M8 1.5c3 3 3 10 0 13" fill="none" stroke="#0455a3" stroke-width="1.2"/></svg>
        <span>www.larkspurtalent.example</span>
      </div>
    </div>

    <div class="person">
      <div class="person-name">Dana Whitby</div>
      <div class="person-title">Manager</div>
    </div>
  </section>

  <section class="card card-back" aria-label="Card back">
    <div class="back-emblem">
      <div class="social">
        <span>Careerloop</span>
        <span>Blipster</span>
        <span>Myriada</span>
      </div>
    </div>
  </section>

</main>
</body>
</html>
```